Business Card Design for Marketing Firm

Looking for business card design for higher end marketing firm. Clean but impressionable/trendy. We are a marketing firm that represents manufacturers in the foodservice equipment and supply industry. Our customers are end users such has hotels, restaurants, country clubs, convention centers and casinos as well as distributors of restaurants supplies and equipment, and manufacturers of foodservice equipment and supplies.
Target Market(s)
Hotels, Restaurants, Supply & Equipment Distributors, Foodservice Manufacturers
Industry/Entity Type
Foodservice/Hospitality
Contact Information for Business Card
Name, Title, Contact Number, Email, Website, Social Media, Address
Requirements
Must have
- Clean & Simple but Serious and Impressionable

```html
<!DOCTYPE html>
<html lang="en">
<head>
<meta charset="utf-8">
<title>Meridian Service Reps — Business Card</title>
<link rel="stylesheet" href="https://fonts.googleapis.com/css2?family=Montserrat:wght@400;500;700&display=swap">
<style>
  :root {
    --navy: #23216a;
    --navy-deep: #1d1c5e;
    --navy-light: #383a82;
    --paper: #f1f1f1;
    --ink: #3a3a3a;
    --backdrop: #e4e4e4;
  }
  * { box-sizing: border-box; margin: 0; padding: 0; }
  html, body { width: 1200px; height: 1200px; overflow: hidden; }
  body {
    background: var(--backdrop);
    font-family: "Montserrat", sans-serif;
    position: relative;
  }
  .card {
    position: absolute;
    left: 234px;
    width: 731px;
    height: 418px;
    overflow: hidden;
  }
  .card-front {
    top: 160px;
    background: linear-gradient(60deg, var(--navy-deep), var(--navy-light));
    display: flex;
    align-items: center;
    justify-content: center;
  }
  .brand {
    display: flex;
    align-items: center;
    gap: 14px;
    font-weight: 500;
    letter-spacing: 0.08em;
    text-transform: uppercase;
  }
  .brand-mark { width: 16px; height: 16px; border-radius: 50%; flex: none; }
  .card-front .brand { color: #ffffff; font-size: 30px; }
  .card-front .brand-mark { background: #ffffff; width: 20px; height: 20px; }

  .card-back { top: 632px; background: var(--paper); }
  .card-back .shapes { position: absolute; inset: 0; }
  .card-back .brand {
    position: absolute;
    left: 40px;
    top: 230px;
    width: 280px;
    justify-content: center;
    color: var(--navy);
    font-size: 17px;
  }
  .card-back .brand-mark { background: var(--navy); }
  .divider {
    position: absolute;
    left: 342px;
    top: 84px;
    width: 2px;
    height: 249px;
    background: var(--navy);
  }
  .contact { position: absolute; left: 374px; top: 80px; color: var(--ink); }
  .person-name { color: var(--navy); font-size: 30px; font-weight: 700; line-height: 36px; }
  .person-title { font-size: 18px; line-height: 24px; margin-top: 2px; }
  .address { font-size: 18.5px; line-height: 26px; margin-top: 24px; }
  .channels { list-style: none; margin-top: 12px; font-size: 18.5px; }
  .channels li { display: flex; align-items: center; gap: 10px; height: 28.5px; }
  .channels svg { width: 15px; height: 15px; flex: none; fill: var(--navy); }
</style>
</head>
<body>
  <section class="card card-front">
    <div class="brand"><span class="brand-mark"></span>Meridian Service Reps</div>
  </section>

  <section class="card card-back">
    <svg class="shapes" viewBox="0 0 731 418" preserveAspectRatio="none" aria-hidden="true">
      <path fill="var(--navy)" d="M0 0 H212 C200 40 172 56 140 62 C92 72 55 108 34 138 C24 150 12 155 0 156 Z"/>
      <path fill="var(--navy)" d="M731 263 C706 270 690 300 670 330 C642 372 604 376 572 385 C546 392 530 402 521 418 H731 Z"/>
    </svg>

    <div class="brand"><span class="brand-mark"></span>Meridian Service Reps</div>
    <div class="divider"></div>

    <div class="contact">
      <h1 class="person-name">Dalton Reese</h1>
      <p class="person-title">Founder &amp; Director</p>
      <p class="address">4178 Harbor Lane<br>Westbrook Maine 04092</p>
      <ul class="channels">
        <li>
          <svg viewBox="0 0 24 24" aria-label="Phone"><path d="M6.6 10.8a15.1 15.1 0 0 0 6.6 6.6l2.2-2.2a1 1 0 0 1 1-.25 11.4 11.4 0 0 0 3.6.57 1 1 0 0 1 1 1V20a1 1 0 0 1-1 1A17 17 0 0 1 3 4a1 1 0 0 1 1-1h3.5a1 1 0 0 1 1 1c0 1.25.2 2.45.57 3.57a1 1 0 0 1-.25 1z"/></svg>
          (207)-555-0148
        </li>
        <li>
          <svg viewBox="0 0 24 24" aria-label="Email"><path d="M2 5h20v14H2z M3 6l9 7 9-7" fill="var(--navy)" stroke="var(--paper)" stroke-width="1.6"/></svg>
          reese@meridianservicereps.com
        </li>
        <li>
          <svg viewBox="0 0 24 24" aria-label="Website"><circle cx="12" cy="12" r="10"/><path d="M2 12h20M12 2c3 3 4 6.5 4 10s-1 7-4 10c-3-3-4-6.5-4-10s1-7 4-10z" fill="none" stroke="var(--paper)" stroke-width="1.6"/></svg>
          www.meridianservicereps.com
        </li>
        <li>
          <svg viewBox="0 0 24 24" aria-label="Social profile"><circle cx="12" cy="12" r="11"/></svg>
          @meridianservicereps
        </li>
      </ul>
    </div>
  </section>
</body>
</html>
```